Custom Manufacturing Company square space website design

I own a custom manufacturing company that uses precision cutting technology to manufacture project components over a couple industries. We have an industrial CNC router and state of the art edge bander and cut a lot of cabinetry components for cabinet shops, builders, closet companies, ect. We offer design and assembly for any cabinetry or can build cabinets to spec. We also cut components for other industries out of wood, plastics, acryclics, ect. We offer design engineering services, product development protype services. we have a 3D printer farm. We want our communicate trust, dependability, and the value we place on client relationships.

We essentially want a credibility website. Landing page and drops downs for services we offer, capabilites, about us, contact

```html
<!DOCTYPE html>
<html lang="en">
<head>
<meta charset="utf-8">
<title>Northgate CNC</title>
<link href="https://fonts.googleapis.com/css2?family=Montserrat:wght@400;500;600;700;800&display=swap" rel="stylesheet">
<style>
:root{
  --ink:#111;
  --text:#333;
  --muted:#555;
  --white:#fff;
  --dark:#141414;
  --band:#1b1b1b;
  --line:#cfcfcf;
}
*{box-sizing:border-box;margin:0;padding:0}
html,body{width:1200px;height:3811px;overflow:hidden}
body{position:relative;font-family:'Montserrat',sans-serif;color:var(--text);background:var(--white)}
.abs{position:absolute}

/* header */
.topbar{position:absolute;left:422px;top:0;width:778px;height:56px;background:var(--ink);clip-path:polygon(0 0,100% 0,100% 100%,28px 100%)}
.topbar .item{position:absolute;top:0;height:56px;display:flex;align-items:center;gap:12px;color:var(--white);font-size:14px;font-weight:700;line-height:1.4}
.brand{position:absolute;left:112px;top:30px;display:flex;align-items:center;gap:12px}
.brand .box{width:46px;height:46px;border:3px solid var(--ink)}
.brand .name{font-size:24px;font-weight:700;letter-spacing:3px;color:var(--ink);line-height:1}
.nav{position:absolute;top:85px;left:484px;display:flex;gap:52px;font-size:15px;font-weight:600;color:var(--ink)}
.nav .active{text-decoration:underline;text-underline-offset:5px}
.nav span.dd::after{content:"";display:inline-block;width:6px;height:6px;border-right:1.5px solid var(--ink);border-bottom:1.5px solid var(--ink);transform:rotate(45deg);margin-left:6px;position:relative;top:-3px}
.btn-contact{position:absolute;left:1012px;top:77px;width:112px;height:36px;background:var(--ink);color:var(--white);font-size:15px;font-weight:700;display:flex;align-items:center;justify-content:center}

/* hero */
.hero{position:absolute;left:0;top:145px;width:1200px;height:549px;background:linear-gradient(90deg,#7d7f80 0%,#5a5b5c 35%,#3f4140 60%,#2e302f 100%)}
.hero-title{position:absolute;left:110px;top:188px;color:var(--white)}
.hero-title .pre{font-size:30px;font-weight:500;letter-spacing:.5px}
.hero-title .main{font-size:45px;font-weight:700;margin-top:2px}
.dots{position:absolute;left:1141px;top:180px;width:5px}
.dots i{display:block;width:5px;height:28px;background:var(--white);margin-bottom:18px}

/* headings */
.h2{font-size:31px;font-weight:700;color:var(--ink)}
.h2.center{position:absolute;left:0;width:1200px;text-align:center}
.h2 .rule{display:block;width:108px;height:4px;background:var(--ink);margin:10px auto 0}

/* about */
.about-title{position:absolute;left:110px;top:776px}
.about-title .rule{display:block;width:108px;height:4px;background:var(--ink);margin-top:4px}
.about-text{position:absolute;left:110px;top:835px;width:447px;font-size:14px;line-height:31px;text-align:justify}
.btn-dark{position:absolute;background:var(--ink);color:var(--white);font-size:15px;font-weight:700;display:flex;align-items:center;justify-content:center}
.about-shadow{position:absolute;left:660px;top:820px;width:418px;height:315px;border-right:5px solid var(--ink);border-bottom:5px solid var(--ink)}
.about-photo{position:absolute;left:645px;top:807px;width:421px;height:314px;background:linear-gradient(135deg,#b28a5e,#6e5b4a 55%,#3c3f47)}

/* cards */
.card{position:absolute;width:308px;height:348px;background:var(--white);box-shadow:0 2px 8px rgba(0,0,0,.25)}
.card .ph{position:absolute;left:10px;top:13px;width:288px;height:283px}
.card .lbl{position:absolute;left:0;width:100%;top:310px;text-align:center;font-size:17px;font-weight:700;color:var(--ink)}
.arrow{position:absolute;width:14px;height:14px;border-left:4px solid var(--ink);border-bottom:4px solid var(--ink)}
.arrow.l{transform:rotate(45deg)}
.arrow.r{transform:rotate(-135deg)}
.arrow.w{border-color:var(--white)}

.caps{position:absolute;left:0;top:1758px;width:1200px;height:502px;background:linear-gradient(180deg,#262626,#161616)}
.caps .h2{color:var(--white)}
.caps .h2 .rule{background:var(--white)}

/* values */
.value{position:absolute;width:330px;text-align:center}
.value .ic{width:90px;height:90px;border-radius:50%;background:var(--ink);margin:0 auto;display:flex;align-items:center;justify-content:center}
.value h3{font-size:19px;font-weight:700;color:var(--ink);margin-top:30px}
.value p{font-size:13px;line-height:26px;color:var(--muted);margin-top:14px}
.vdiv{position:absolute;top:2471px;width:3px;height:304px;background:var(--ink)}

/* contact */
.contact{position:absolute;left:0;top:2871px;width:1200px;height:540px;background:linear-gradient(180deg,#1d1d1d,#101010)}
.contact .h2{color:var(--white);font-size:34px}
.contact .h2 .rule{background:var(--white)}
.field{position:absolute;background:var(--white);border-radius:5px;display:flex;align-items:center;gap:10px;padding-left:14px;font-size:12px;color:#777}
.field.area{align-items:flex-start;padding-top:12px}
.btn-white{position:absolute;left:534px;top:3321px;width:132px;height:38px;background:var(--white);color:var(--ink);font-size:15px;font-weight:700;display:flex;align-items:center;justify-content:center}

/* footer */
.fbrand{position:absolute;left:112px;top:3552px;display:flex;align-items:center;gap:14px}
.fbrand .box{width:58px;height:58px;border:3px solid var(--ink)}
.fbrand .name{font-size:27px;font-weight:700;letter-spacing:3px;color:var(--ink)}
.fcol{position:absolute;top:3510px;font-size:16px;color:var(--ink)}
.fcol h4{font-size:17px;font-weight:700;margin-bottom:12px}
.fcol a{display:block;line-height:37px;text-decoration:none;color:var(--ink)}
.fcol .row{display:flex;gap:12px;align-items:flex-start;margin-bottom:18px;line-height:24px}
.sq{display:inline-block;width:18px;height:18px;border:2px solid var(--ink);vertical-align:middle;margin-right:12px}
.fline{position:absolute;left:112px;top:3766px;width:976px;height:1px;background:#888}
.copy{position:absolute;left:0;width:1200px;top:3780px;text-align:center;font-size:15px;color:var(--ink)}
</style>
</head>
<body>

<header>
  <div class="topbar">
    <div class="item" style="left:54px">
      <svg width="22" height="24" viewBox="0 0 22 24"><rect x="0" y="1" width="22" height="22" rx="3" fill="#fff"/><path d="M11 5a5 5 0 0 0-5 5c0 4 5 9 5 9s5-5 5-9a5 5 0 0 0-5-5z" fill="#111"/><circle cx="11" cy="10" r="2" fill="#fff"/></svg>
      <span>218 Harlow Ave NE<br>Millbrook, MN 55990</span>
    </div>
    <div class="item" style="left:313px">
      <svg width="22" height="22" viewBox="0 0 22 22"><rect width="22" height="22" rx="3" fill="#fff"/><path d="M7 5l3 3-2 2c1 2 2 3 4 4l2-2 3 3-2 2C9 17 5 13 5 7z" fill="#111"/></svg>
      <span>(555) 014-2290</span>
    </div>
    <div class="item" style="left:518px">
      <svg width="22" height="20" viewBox="0 0 22 20"><rect width="22" height="20" rx="3" fill="#fff"/><rect x="4" y="5" width="14" height="10" fill="none" stroke="#111" stroke-width="1.6"/><path d="M4 5l7 6 7-6" fill="none" stroke="#111" stroke-width="1.6"/></svg>
      <span>info@northgatecnc.com</span>
    </div>
  </div>
  <div class="brand"><span class="box"></span><span class="name">NORTHGATE CNC</span></div>
  <nav class="nav">
    <span class="active">Home</span>
    <span class="dd">Industries</span>
    <span class="dd">Capabilities</span>
    <span class="dd">About Us</span>
  </nav>
  <div class="btn-contact">CONTACT</div>
</header>

<section class="hero" role="img" aria-label="Modern dark kitchen with black cabinetry and a grey island">
  <div class="hero-title">
    <div class="pre">WELCOME TO</div>
    <div class="main">NORTHGATE CNC</div>
  </div>
  <div class="dots"><i></i><i></i><i></i></div>
</section>

<section class="about">
  <h2 class="h2 about-title">ABOUT US<span class="rule"></span></h2>
  <p class="about-text">Lorem ipsum dolor sit amet, consectetur adipiscing elit, sed do eiusmod tempor incididunt ut labore et dolore magna aliqua. Ut enim ad minim veniam, quis nostrud exercitation ullamco laboris nisi ut aliquip ex ea commodo consequat. Duis aute irure dolor in reprehenderit in voluptate velit esse cillum dolore eu fugiat nulla pariatur. Excepteur sint occaecat cupidatat non proident, sunt in culpa qui officia deserunt mollit anim id est laborum</p>
  <div class="btn-dark" style="left:109px;top:1090px;width:132px;height:37px">READ MORE</div>
  <div class="about-shadow"></div>
  <div class="about-photo" role="img" aria-label="Worker assembling a wooden shelving unit"></div>
</section>

<section class="industries">
  <h2 class="h2 center" style="top:1226px">INDUSTRIES<span class="rule"></span></h2>
  <span class="arrow l" style="left:52px;top:1488px"></span>
  <div class="card" style="left:112px;top:1314px"><div class="ph" role="img" aria-label="White kitchen cabinetry" style="background:linear-gradient(180deg,#d9d9d7,#f1f0ee 50%,#c9c7c3)"></div><div class="lbl">CABINETRY</div></div>
  <div class="card" style="left:445px;top:1314px"><div class="ph" role="img" aria-label="Builder fitting a wooden panel in a kitchen" style="background:linear-gradient(180deg,#eeeeec,#e2d3bd 60%,#b9b4ac)"></div><div class="lbl">BUILDERS</div></div>
  <div class="card" style="left:777px;top:1314px"><div class="ph" role="img" aria-label="Red CNC machine cutting sheet material in a workshop" style="background:linear-gradient(135deg,#c9b99a,#d0503c 45%,#6b5f4c)"></div><div class="lbl">CUSTOM MANUFACTURING</div></div>
  <span class="arrow r" style="left:1127px;top:1488px"></span>
</section>

<section class="caps">
  <h2 class="h2 center" style="top:40px">CAPABILITIES<span class="rule"></span></h2>
  <span class="arrow l w" style="left:52px;top:282px"></span>
  <div class="card" style="left:112px;top:107px"><div class="ph" role="img" aria-label="CNC router spindle over a wooden board" style="background:linear-gradient(135deg,#3a3a3a,#c8582f 45%,#c89a6a)"></div><div class="lbl">CNC ROUTING</div></div>
  <div class="card" style="left:445px;top:107px"><div class="ph" role="img" aria-label="Edge banding machine in a clean shop" style="background:linear-gradient(180deg,#ececea,#9a9a98 55%,#3e4a7a)"></div><div class="lbl">EDGE BANDING</div></div>
  <div class="card" style="left:777px;top:107px"><div class="ph" role="img" aria-label="Engineer working with a 3D printer" style="background:linear-gradient(135deg,#8a8a88,#2f3240 55%,#6a6a66)"></div><div class="lbl">DESIGN ENGINEERING</div></div>
  <span class="arrow r w" style="left:1127px;top:282px"></span>
</section>

<section class="values">
  <h2 class="h2 center" style="top:2350px">VALUES<span class="rule"></span></h2>
  <div class="value" style="left:91px;top:2459px">
    <div class="ic"><svg width="40" height="40" viewBox="0 0 40 40" fill="#fff"><circle cx="12" cy="22" r="4"/><path d="M5 36c0-5 3-8 7-8s7 3 7 8z"/><circle cx="28" cy="8" r="4"/><path d="M21 22c0-5 3-8 7-8s7 3 7 8z"/><path d="M8 13a8 8 0 0 1 8-8l-2-2m2 2-2 2" stroke="#fff" stroke-width="2" fill="none"/></svg></div>
    <h3>COMMUNICATION</h3>
    <p>Communication At the heart of any good relationship is communication. We make sure we are available to our clients and understand the importance of affective communication to problem solve and move the ball forward with every project.</p>
  </div>
  <div class="vdiv" style="left:437px"></div>
  <div class="value" style="left:446px;top:2459px">
    <div class="ic"><svg width="46" height="40" viewBox="0 0 46 40" fill="none" stroke="#fff" stroke-width="2.5"><path d="M23 3l8 3v6c0 5-4 8-8 9-4-1-8-4-8-9V6z"/><path d="M19 12l3 3 5-5"/><path d="M3 22l8-4 6 4h8l-8 8-4-2M43 22l-8-4-6 4"/><path d="M17 30l6 5 12-11"/></svg></div>
    <h3>DEPENDABILITY</h3>
    <p>Dependability Trust is built through time and action. Our team is dedicated to ensuring that promises made are promises kept. From the precision in our manufacturing process to the punctualities of our deliveries, dependability is woven into every aspect of our work</p>
  </div>
  <div class="vdiv" style="left:808px"></div>
  <div class="value" style="left:806px;top:2459px">
    <div class="ic"><svg width="42" height="42" viewBox="0 0 42 42" fill="none" stroke="#fff" stroke-width="2.5"><path d="M10 38v-8c-4-3-6-7-6-12A16 16 0 0 1 36 17l3 6h-3v6c0 3-2 4-5 4h-3v5"/><path d="M20 23l-5-5a3 3 0 0 1 5-4 3 3 0 0 1 5 4z" fill="#fff"/></svg></div>
    <h3>CREATING VALUE</h3>
    <p>Creating Value Creating value is not only a goal at Northgate CNC, it's our guiding principle. We believe true success lies not only in the products we manufacture but in the lasting value we provide our clients.</p>
  </div>
</section>

<section class="contact">
  <h2 class="h2 center" style="top:44px">CONTACT US<span class="rule"></span></h2>
</section>
<form>
  <div class="field" style="left:144px;top:3010px;width:448px;height:45px"><svg width="14" height="14" viewBox="0 0 14 14" fill="#111"><circle cx="7" cy="4" r="3.2"/><path d="M1 14c0-4 3-6 6-6s6 2 6 6z"/></svg>Name</div>
  <div class="field" style="left:613px;top:3010px;width:451px;height:45px"><svg width="16" height="12" viewBox="0 0 16 12"><rect x="1" y="1" width="14" height="10" fill="none" stroke="#111" stroke-width="1.5"/><path d="M1 1l7 6 7-6" fill="none" stroke="#111" stroke-width="1.5"/></svg>Email</div>
  <div class="field" style="left:144px;top:3069px;width:448px;height:46px"><svg width="14" height="14" viewBox="0 0 14 14" fill="#111"><path d="M3 1l3 3-2 2c1 2 2 3 4 4l2-2 3 3-2 2C6 13 1 8 1 3z"/></svg>Contact Number</div>
  <div class="field" style="left:613px;top:3069px;width:451px;height:46px"><svg width="14" height="14" viewBox="0 0 14 14"><rect x="2" y="1" width="10" height="12" fill="none" stroke="#111" stroke-width="1.6"/><path d="M2 1v12" stroke="#111" stroke-width="3"/></svg>Subject</div>
  <div class="field area" style="left:144px;top:3130px;width:920px;height:164px"><svg width="16" height="14" viewBox="0 0 16 14" fill="#111"><ellipse cx="8" cy="6" rx="7.5" ry="5.5"/><path d="M3 10l-1 4 4-2z"/><circle cx="5" cy="6" r="1" fill="#fff"/><circle cx="8" cy="6" r="1" fill="#fff"/><circle cx="11" cy="6" r="1" fill="#fff"/></svg>Your Messsage</div>
  <div class="btn-white">SUBMIT</div>
</form>

<footer>
  <div class="fbrand"><span class="box"></span><span class="name">NORTHGATE CNC</span></div>
  <div class="fcol" style="left:459px">
    <h4>QUICK LINKS</h4>
    <a>Home</a><a>Industries</a><a>Capabilities</a><a>About Us</a><a>Contact</a>
  </div>
  <div class="fcol" style="left:651px">
    <h4>HELP LINKS</h4>
    <a>Privacy Policy</a><a>Terms &amp; Conditions</a>
    <h4 style="margin-top:16px">FOLLOW US</h4>
    <a><span class="sq"></span>Social Page</a>
    <a><span class="sq"></span>Photo Feed</a>
  </div>
  <div class="fcol" style="left:884px">
    <h4>CONTACT DETAIL</h4>
    <div class="row"><svg width="24" height="24" viewBox="0 0 22 24"><rect x="0" y="1" width="22" height="22" rx="3" fill="#111"/><path d="M11 5a5 5 0 0 0-5 5c0 4 5 9 5 9s5-5 5-9a5 5 0 0 0-5-5z" fill="#fff"/><circle cx="11" cy="10" r="2" fill="#111"/></svg><span>218 Harlow Ave NE,<br>Millbrook, MN 55990</span></div>
    <div class="row"><svg width="22" height="22" viewBox="0 0 22 22"><rect width="22" height="22" rx="3" fill="#111"/><path d="M7 5l3 3-2 2c1 2 2 3 4 4l2-2 3 3-2 2C9 17 5 13 5 7z" fill="#fff"/></svg><span>(555) 014-2290</span></div>
    <div class="row"><svg width="22" height="20" viewBox="0 0 22 20"><rect width="22" height="20" rx="3" fill="#111"/><rect x="4" y="5" width="14" height="10" fill="none" stroke="#fff" stroke-width="1.6"/><path d="M4 5l7 6 7-6" fill="none" stroke="#fff" stroke-width="1.6"/></svg><span>info@northgatecnc.com</span></div>
  </div>
  <div class="fline"></div>
  <div class="copy">© 2023 Northgate CNC. All rights reserved.</div>
</footer>

</body>
</html>
```